Website Redesign for an Appointment Setting and Lead Generation Company.

I need to redesign an existing website. The website that we are looking to be redesigned is www.farlinqo.com. FarLinqo is a B2B appointment setting organization. The idea is to present a modern look website for professional services company. The idea is to engage the user, look at various services and generate more inbound leads for the website

Target Market(s)

US, APAC, Europe, UK. Focused on B2B companies more than $100 Mn

Industry/Entity Type

Professional Service

Number of Pages Required

5+ page

Font styles to use
Other font styles liked:
• Roboto

Requirements
Must have
• Home Page - Banner Image, Section for Client testimonials
Industry Page - To show industry capabilities
Services Page - To show service capabilities
Blogs Page - to show blogs
Offerings Page - Offerings Page
Nice to have
• I would like to have a elegant design with small animation. Preferably use colors from the logo attached. Use infographics where possible

```html
<!DOCTYPE html>
<html lang="en">
<head>
<meta charset="utf-8">
<title>FarLinqo – Blog</title>
<link href="https://fonts.googleapis.com/css2?family=Roboto:wght@300;400;500;700&display=swap" rel="stylesheet">
<style>
:root{
  --red:#c4262e;
  --ink:#333333;
  --muted:#8a8a8a;
  --line:#dddddd;
  --panel:#f6f6f6;
  --band:#f4f4f4;
  --white:#ffffff;
}
*{box-sizing:border-box;margin:0;padding:0}
html,body{width:1200px;height:3855px;overflow:hidden}
body{position:relative;background:var(--white);font-family:'Roboto',sans-serif;color:var(--ink)}
.abs{position:absolute}

/* header */
.brand{position:absolute;font-family:'Roboto',sans-serif;font-weight:500;color:var(--red);display:flex;align-items:center;gap:8px}
.brand .dot{width:14px;height:14px;background:var(--red);border-radius:50%}
.site-brand{left:125px;top:16px;font-size:24px}
.nav{position:absolute;left:466px;top:26px;display:flex;gap:22px;font-size:14px;color:#777}
.nav span.drop::after{content:"";display:inline-block;width:5px;height:5px;border-right:1px solid #aaa;border-bottom:1px solid #aaa;transform:rotate(45deg);margin:0 0 3px 6px}
.nav .active{color:var(--red)}
.search-icon{left:1060px;top:24px}

/* hero */
.hero{left:90px;top:90px;width:1020px;height:505px;background:linear-gradient(180deg,#8e8f93 0%,#7c7d81 60%,#6f6f72 100%)}
.hero-welcome{left:463px;top:184px;color:#fff;font-size:16px;font-weight:500}
.hero-name{left:508px;top:204px;font-size:28px;font-weight:300;color:rgba(255,255,255,.55)}
.hero-title{left:563px;top:250px;color:#fff;font-size:38px;font-weight:500}
.hero-caption{left:130px;top:482px;color:#fff;font-size:15px;line-height:23px;letter-spacing:.5px}
.hero-meta{left:130px;top:543px;display:flex;align-items:center;gap:14px;color:#fff;font-size:12px;font-weight:500}
.hero-meta .sq{width:20px;height:20px;background:#fff;border-radius:2px}
.hero-meta .gap{width:16px}
.slide-arrow{width:40px;height:40px;background:#fff;top:312px;box-shadow:0 1px 3px rgba(0,0,0,.15);display:flex;align-items:center;justify-content:center}
.side-social{left:1140px;top:460px;display:flex;flex-direction:column;gap:22px}
.side-social i{display:block;width:20px;height:16px;border:1.5px solid #e2e2e2;border-radius:3px}

/* section heading */
.watermark{left:0;width:1200px;top:676px;text-align:center;font-size:110px;font-weight:300;color:rgba(0,0,0,.035);letter-spacing:2px}
.section-title{left:547px;top:785px;font-size:28px;font-weight:400;letter-spacing:2px;padding-left:20px}
.section-title::before{content:"";position:absolute;left:0;top:4px;width:6px;height:28px;background:var(--red)}

/* posts */
.post-grid{left:126px;top:871px;display:grid;grid-template-columns:297px 297px;column-gap:69px;grid-auto-rows:298px}
.post-thumb{display:block;height:127px}
.post-title{margin-top:18px;height:36px;font-size:12px;line-height:16px;letter-spacing:.3px}
.post-meta{margin-top:12px;display:flex;justify-content:space-between;font-size:12px;color:var(--muted);letter-spacing:.5px}
.read-more{display:block;margin-top:16px;font-size:12px;color:var(--red);text-decoration:none}

/* sidebar */
.sidebar{left:895px;top:871px;width:272px;height:680px;background:var(--panel)}
.search-box{position:absolute;left:25px;top:45px;width:222px;height:48px;border:2px solid #e3e3e3;background:#fff;font-size:12px;color:#aaa;padding:17px 24px}
.side-head{position:absolute;left:27px;font-size:13px;color:var(--ink);width:218px;padding-bottom:12px;border-bottom:1px solid #ddd}
.side-icons{position:absolute;left:27px;top:212px;display:flex;gap:22px}
.side-icons i{width:14px;height:14px;border-radius:50%;background:#e4e4e4}
.latest{position:absolute;left:27px;width:245px;display:flex;gap:13px}
.latest .thumb{width:66px;height:66px;flex:none}
.latest p{font-size:12px;line-height:15.5px;color:var(--ink);padding-top:2px}

/* pagination */
.pager-line{left:130px;top:2387px;width:660px;height:1px;background:var(--line)}
.pager{left:278px;top:2418px;display:flex;align-items:center}
.pager .arrow{width:10px;height:10px;border-left:1px solid #999;border-bottom:1px solid #999}
.pager .prev{transform:rotate(45deg);margin-right:56px}
.pager .next{transform:rotate(-135deg);margin-left:50px}
.pager .page{width:36px;height:36px;margin-right:26px;background:#fff;box-shadow:0 1px 4px rgba(0,0,0,.18);font-size:16px;display:flex;align-items:center;justify-content:center}
.pager .page.current{color:var(--red)}
.pager .page:last-of-type{margin-right:0}

/* contact */
.contact-band{left:0;top:2700px;width:1200px;height:552px;background:var(--band)}
.contact-card{left:328px;top:2592px;width:545px;height:770px;background:#fff;box-shadow:0 2px 10px rgba(0,0,0,.06)}
.contact-title{position:absolute;left:0;width:545px;top:38px;text-align:center;font-size:19px;color:#555}
.field{position:absolute;height:20px;border-bottom:1px solid #bbb;font-size:11px;color:#aaa}
.field::after{content:"*";position:absolute;right:-6px;top:0;color:var(--red)}
.field.message{border-bottom-color:#999}
.field.message::after{content:none}
.consent{position:absolute;left:74px;font-size:12px;line-height:23px;color:#555}
.consent a{color:var(--red);text-decoration:none}
.checkbox{position:absolute;left:74px;top:366px;width:10px;height:10px;border:1px solid #777}
.submit{position:absolute;left:74px;top:665px;width:127px;height:43px;background:#333;color:#fff;font-size:14px;display:flex;align-items:center;justify-content:center;box-shadow:0 2px 4px rgba(0,0,0,.25)}

/* footer */
.footer-brand{left:155px;top:3416px;font-size:28px}
.footer-social{left:155px;top:3562px;display:flex;gap:48px}
.footer-social i{width:20px;height:20px;border:1.5px solid #999;border-radius:50%}
.footer-col{top:3416px}
.footer-col h4{font-size:16px;font-weight:500;color:var(--red);padding-bottom:6px;display:inline-block;border-bottom:3px solid var(--red);letter-spacing:.3px}
.footer-col ul{list-style:none;margin-top:12px}
.footer-col li{font-size:14px;color:#444;height:39.5px;line-height:20px}
.to-top{left:1107px;top:3709px;width:44px;height:44px;border-radius:50%;background:#fff;box-shadow:0 1px 6px rgba(0,0,0,.15)}
.to-top::after{content:"";position:absolute;left:18px;top:19px;width:8px;height:8px;border-left:1px solid #c55;border-top:1px solid #c55;transform:rotate(45deg)}
.copyright{left:0;top:3787px;width:1200px;height:68px;background:#e3e3e3;display:flex;align-items:center;justify-content:center;font-size:11px;font-weight:500;color:#333}
.copyright .sep{width:2px;height:18px;background:var(--red);margin:0 16px}
.copyright a{color:var(--red);text-decoration:none}
</style>
</head>
<body>

<header>
  <div class="brand site-brand"><span class="dot"></span>FarLinqo</div>
  <nav class="nav">
    <span>Home</span><span class="drop">About</span><span class="drop">Services</span><span class="drop">Our Expertise</span><span class="drop active">Library</span><span class="drop">Contact Us</span>
  </nav>
  <svg class="abs search-icon" width="20" height="20" viewBox="0 0 20 20" fill="none" stroke="#333" stroke-width="1.6"><circle cx="8.5" cy="8.5" r="6.5"/><line x1="13.5" y1="13.5" x2="18" y2="18"/></svg>
</header>

<section>
  <div class="abs hero" role="img" aria-label="Photo of a businessman meditating cross-legged on an office chair against a grey wall"></div>
  <div class="abs hero-welcome">Welcome to</div>
  <div class="abs hero-name">FarLinqo</div>
  <div class="abs hero-title">Blog</div>
  <div class="abs hero-caption">Amplifying &amp; Simplifying B2B Sales<br>Through Outsourcing</div>
  <div class="abs hero-meta"><span class="sq"></span><span class="sq"></span><span class="sq"></span><span class="gap"></span><span>5 mins read</span><span class="gap"></span><span>10,May,2020</span></div>
  <div class="abs slide-arrow" style="left:70px"><svg width="10" height="14" viewBox="0 0 10 14" fill="none" stroke="#999"><polyline points="8,1 2,7 8,13"/></svg></div>
  <div class="abs slide-arrow" style="left:1090px"><svg width="10" height="14" viewBox="0 0 10 14" fill="none" stroke="#999"><polyline points="2,1 8,7 2,13"/></svg></div>
  <div class="abs side-social"><i></i><i></i><i></i><i></i></div>
</section>

<section>
  <div class="abs watermark">FarLinqo</div>
  <h2 class="abs section-title">Blog</h2>

  <div class="abs post-grid">
    <article><div class="post-thumb" role="img" aria-label="Hand holding a bouquet of folded banknotes" style="background:linear-gradient(90deg,#c9c6b8,#e8e8e6)"></div><h3 class="post-title" style="font-weight:400">Sales Cadence Elements That Can TurnYour Sales Game</h3><div class="post-meta"><span>5 mins read</span><span>10,May,2020</span></div><a class="read-more">Read More</a></article>
    <article><div class="post-thumb" role="img" aria-label="Hand placing wooden blocks on a table" style="background:linear-gradient(90deg,#e9dfcf,#cdb89a)"></div><h3 class="post-title" style="font-weight:400">Taking The Right Sales Approach: Outbound or Inbound ?</h3><div class="post-meta"><span>5 mins read</span><span>10,May,2020</span></div><a class="read-more">Read More</a></article>
    <article><div class="post-thumb" role="img" aria-label="Megaphone on a bright yellow background" style="background:radial-gradient(circle at 45% 40%,#fff6d8,#f7cf45 55%,#f3c12b)"></div><h3 class="post-title" style="font-weight:400">Achieving Sales Target Through The Referral Road</h3><div class="post-meta"><span>5 mins read</span><span>10,May,2020</span></div><a class="read-more">Read More</a></article>
    <article><div class="post-thumb" role="img" aria-label="Dark image of a sales process chart with share options" style="background:linear-gradient(90deg,#1c1c1e,#2f3034)"></div><h3 class="post-title" style="font-weight:400">Reigniting Sales: 5 Ways To Warm Up Cold Leads</h3><div class="post-meta"><span>5 mins read</span><span>10,May,2020</span></div><a class="read-more">Read More</a></article>
    <article><div class="post-thumb" role="img" aria-label="Businessman meditating on an office chair" style="background:linear-gradient(180deg,#a5a7ab,#8b8d91)"></div><h3 class="post-title" style="font-weight:400">Amplifying &amp; Simplifying B2B Sales Through Outsourcing</h3><div class="post-meta"><span>5 mins read</span><span>10,May,2020</span></div><a class="read-more">Read More</a></article>
    <article><div class="post-thumb" role="img" aria-label="Football match in a floodlit stadium" style="background:linear-gradient(180deg,#2b4f86,#3e6aa3 55%,#3f7a3a)"></div><h3 class="post-title" style="font-weight:400">Getting Past The Gatekeeper: An Art To Master</h3><div class="post-meta"><span>5 mins read</span><span>10,May,2020</span></div><a class="read-more">Read More</a></article>
    <article><div class="post-thumb" role="img" aria-label="Chess pieces on a printed lead prospecting board" style="background:linear-gradient(90deg,#5a5b5e,#7b7c80)"></div><h3 class="post-title" style="font-weight:400">Creating an Edge Over B2B Sales Prospecting Tactics For The New Age Buyer</h3><div class="post-meta"><span>5 mins read</span><span>10,May,2020</span></div><a class="read-more">Read More</a></article>
    <article><div class="post-thumb" role="img" aria-label="Woman with a headset working at a laptop in a bright office" style="background:linear-gradient(90deg,#f1f1ee,#d9d6d0)"></div><h3 class="post-title" style="font-weight:400">Productive Planning To Drive More Attendees For Webinars</h3><div class="post-meta"><span>5 mins read</span><span>10,May,2020</span></div><a class="read-more">Read More</a></article>
    <article><div class="post-thumb" role="img" aria-label="Man with headphones gesturing during a video call" style="background:linear-gradient(90deg,#d7d3cb,#8e9aa6)"></div><h3 class="post-title" style="font-weight:400">Brimming Optimism: Europe Positive to Remote Selling Strategy</h3><div class="post-meta"><span>5 mins read</span><span>10,May,2020</span></div><a class="read-more">Read More</a></article>
    <article><div class="post-thumb" role="img" aria-label="Colleagues discussing around a laptop in an office" style="background:linear-gradient(90deg,#bfc3c7,#eeeeee 50%,#9ea3a8)"></div><h3 class="post-title" style="font-weight:400">Rethinking Lead Generation: A Marketer's Perspective</h3><div class="post-meta"><span>5 mins read</span><span>10,May,2020</span></div><a class="read-more">Read More</a></article>
  </div>

  <aside class="abs sidebar">
    <div class="search-box">Search</div>
    <div class="side-head" style="top:156px">Follow Us</div>
    <div class="side-icons"><i></i><i></i><i></i></div>
    <div class="side-head" style="top:315px">Latest Posts</div>
    <div class="latest" style="top:367px"><div class="thumb" role="img" aria-label="Wooden blocks" style="background:linear-gradient(90deg,#e9dfcf,#b99f7d)"></div><p>Taking The Right Sales Approach: Outbound or Inbound ?</p></div>
    <div class="latest" style="top:455px"><div class="thumb" role="img" aria-label="Dark sales chart" style="background:linear-gradient(90deg,#22242a,#3d4a63)"></div><p>Taking The Right Sales Approach: Outbound or Inbound ?</p></div>
    <div class="latest" style="top:543px"><div class="thumb" role="img" aria-label="Football stadium" style="background:linear-gradient(180deg,#2b4f86,#3f7a3a)"></div><p>Taking The Right Sales Approach: Outbound or Inbound ?</p></div>
  </aside>

  <div class="abs pager-line"></div>
  <div class="abs pager">
    <span class="arrow prev"></span>
    <span class="page current">1</span><span class="page">2</span><span class="page">3</span><span class="page">4</span>
    <span class="arrow next"></span>
  </div>
</section>

<section>
  <div class="abs contact-band"></div>
  <div class="abs contact-card">
    <h2 class="contact-title" style="font-weight:400">Contact Us</h2>
    <div class="field" style="left:74px;top:108px;width:168px">First name</div>
    <div class="field" style="left:303px;top:108px;width:164px">Email</div>
    <div class="field" style="left:74px;top:155px;width:168px">Last name</div>
    <div class="field" style="left:303px;top:155px;width:164px">Phone number</div>
    <div class="field" style="left:74px;top:202px;width:195px">Company name</div>
    <div class="field message" style="left:74px;top:311px;width:393px">Message</div>
    <div class="checkbox"></div>
    <p class="consent" style="left:100px;top:357px">I agree to receive other communications<br>from FarLinqo.</p>
    <p class="consent" style="top:420px;width:410px">You can unsubscribe from these communications at anytime. For more information on how to unsubscribe, our privacy practices, and how we are committed to protecting and respecting your privacy, please review our <a>Privacy Policy</a>.</p>
    <p class="consent" style="top:532px;width:240px">By clicking submit below, you consent to allow FarLinqo to store and process the personal information submitted above to provide you the content requested.</p>
    <div class="submit">Submit</div>
  </div>
</section>

<footer>
  <div class="brand footer-brand abs"><span class="dot"></span>FarLinqo</div>
  <div class="abs footer-social"><i></i><i></i><i></i></div>
  <div class="abs footer-col" style="left:493px"><h4>ABOUT US</h4><ul><li>About</li><li>Our Team</li><li>Awards</li><li>Our Partnerships</li><li>Our Differentiators</li><li>Locations</li></ul></div>
  <div class="abs footer-col" style="left:692px"><h4>SERVICES</h4><ul><li>B2B Appointment Setting</li><li>Account Based Marketing</li><li>Research As A Service</li><li>Event Audience Acquisition</li><li>Staffing &amp; Talent Acquisition</li><li>Digital Marketing</li><li>Social Media Research</li><li>Lead Nurturing</li></ul></div>
  <div class="abs footer-col" style="left:959px"><h4>LIBRARY</h4><ul><li>Videos</li><li>Infographics</li><li>Blog</li><li>Case Studies</li></ul></div>
  <div class="abs to-top"></div>
  <div class="abs copyright"><span>Copyright All Rights Reserved © 2020.</span><span class="sep"></span><a>Privacy Policy</a></div>
</footer>

</body>
</html>
```